Storm Restoration Contractor needs a professional letterhead design

Looking for a professional letterhead design. Not looking for your cheapo MS Word standard ones that are readily available. Dont want it to be cookie cutter look like ones readily available online. We just recently changed our logo and want to freshen up all our documents. Our company handles restoring a property back to a pre-loss condition after a storm damages it. For example, wind, hail, flood, fire losses.

Target Market(s)

Property Owners, Homeowners, Property Owners, Commercial Property Owners, Property Management Companies

Industry/Entity Type

Construction Company

Requirements
Must have
• Professional, Use 1 of 2 logo options
• Storm Restoration, Roofing, Siding, Windows

```html
<!DOCTYPE html>
<html lang="en">
<head>
<meta charset="utf-8">
<title>Northgate Exteriors — Letterhead</title>
<link href="https://fonts.googleapis.com/css2?family=Questrial&display=swap" rel="stylesheet">
<style>
  :root {
    --backdrop: #bdbdbd;
    --paper: #f1f1f1;
    --brand-blue: #2470bd;
    --ink: #3f3f3f;
    --faint-mark: #e6e6e6;
  }
  * { margin: 0; padding: 0; box-sizing: border-box; }
  html, body {
    width: 1200px;
    height: 1041px;
    overflow: hidden;
    background: var(--backdrop);
    font-family: "Questrial", "Century Gothic", sans-serif;
  }
  .letterhead {
    position: absolute;
    left: 280px;
    top: 106px;
    width: 640px;
    height: 826px;
    background: var(--paper);
    box-shadow: 0 2px 6px rgba(0,0,0,0.25);
    overflow: hidden;
  }
  .top-swoosh {
    position: absolute;
    left: 0;
    top: 0;
    width: 640px;
    height: 16px;
  }
  .brand {
    position: absolute;
    left: 0;
    top: 118px;
    width: 100%;
    display: flex;
    justify-content: center;
    align-items: center;
    gap: 10px;
  }
  .brand-dot {
    width: 14px;
    height: 14px;
    border-radius: 50%;
    background: var(--brand-blue);
  }
  .brand-name {
    font-size: 17px;
    letter-spacing: 2px;
    color: var(--brand-blue);
    text-transform: uppercase;
  }
  .background-mark {
    position: absolute;
    left: 122px;
    top: 262px;
    width: 396px;
    height: 396px;
  }
  .footer {
    position: absolute;
    left: 0;
    top: 742px;
    width: 100%;
    text-align: center;
    color: var(--ink);
  }
  .contact-icons {
    display: block;
    margin: 0 auto;
    width: 140px;
    height: 22px;
  }
  .address {
    margin-top: 10px;
    font-size: 8.6px;
  }
  .contact-line {
    margin-top: 5px;
    font-size: 8.6px;
  }
  .contact-line .sep {
    color: var(--brand-blue);
    margin: 0 6px;
  }
</style>
</head>
<body>
  <main class="letterhead">
    <svg class="top-swoosh" viewBox="0 0 640 16" aria-hidden="true">
      <path d="M56 0 Q320 24 584 0 Z" fill="var(--brand-blue)"/>
    </svg>

    <header class="brand">
      <span class="brand-dot"></span>
      <span class="brand-name">Northgate Exteriors</span>
    </header>

    <svg class="background-mark" viewBox="0 0 396 396" aria-hidden="true">
      <circle cx="198" cy="198" r="198" fill="var(--faint-mark)"/>
    </svg>

    <footer class="footer">
      <svg class="contact-icons" viewBox="0 0 140 22" aria-hidden="true" fill="none" stroke="var(--brand-blue)" stroke-width="1.2">
        <line x1="0" y1="11" x2="140" y2="11"/>
        <g fill="var(--paper)">
          <circle cx="31" cy="11" r="8.5"/>
          <circle cx="57" cy="11" r="8.5"/>
          <circle cx="83" cy="11" r="8.5"/>
          <circle cx="109" cy="11" r="8.5"/>
        </g>
        <!-- home -->
        <path d="M26.5 11.5 L31 7.2 L35.5 11.5 M28 10.5 V15 H34 V10.5" fill="var(--brand-blue)" stroke-linejoin="round"/>
        <!-- phone -->
        <path d="M54.5 7 Q53.5 8 54.5 10.5 Q56 13.5 59 15 Q60.5 15.5 61 14.5 L59.5 13 L58.5 13.7 Q56.5 12.5 55.8 10.6 L56.6 9.6 Z" fill="var(--brand-blue)" stroke-width="0.6"/>
        <!-- mail -->
        <rect x="78.5" y="7.8" width="9" height="6.4" fill="var(--brand-blue)" stroke-width="0.6"/>
        <path d="M78.5 7.8 L83 11.4 L87.5 7.8" stroke="var(--paper)" stroke-width="0.8"/>
        <!-- globe -->
        <circle cx="109" cy="11" r="4.6" stroke-width="0.9"/>
        <ellipse cx="109" cy="11" rx="2" ry="4.6" stroke-width="0.8"/>
        <line x1="104.4" y1="11" x2="113.6" y2="11" stroke-width="0.8"/>
      </svg>
      <p class="address">4120 E Canyon Ridge Road STE 210, Mesa, AZ 85201</p>
      <p class="contact-line">555-014-2700<span class="sep">|</span>info@northgateext.com<span class="sep">|</span>www.northgateext.com</p>
    </footer>
  </main>
</body>
</html>
```